Business Card for a Dental Office

The design should communicate integrity, quality and reliability. We also want the card look elegant, simple, but still stand out, different from the traditional-dental-office business card.

Industry/Entity Type

Business

```html
<!DOCTYPE html>
<html lang="en">
<head>
<meta charset="utf-8">
<title>Harwell Dental Studio – Business Card</title>
<link rel="stylesheet" href="https://fonts.googleapis.com/css2?family=Source+Sans+3:wght@400;600;700&display=swap">
<style>
  :root {
    --ink: #111111;
    --paper: #ffffff;
    --gold: #c6a61f;
    --gold-text: #c9a91c;
    --gold-deep: #b79b1d;
    --yellow: #f7ee2a;
    --backdrop: #e9e6e3;
  }
  * { margin: 0; padding: 0; box-sizing: border-box; }
  html, body {
    width: 1200px; height: 900px; overflow: hidden;
    background: var(--backdrop);
    font-family: "Source Sans 3", "Myriad Pro", Arial, sans-serif;
    color: var(--ink);
  }
  .canvas { position: relative; width: 1200px; height: 900px; }

  .card {
    position: absolute;
    background: var(--paper);
    overflow: hidden;
    box-shadow: 0 6px 18px rgba(0,0,0,0.18);
  }
  .card-front { left: 78px; top: 35px; width: 587px; height: 363px; }
  .card-back  { left: 389px; top: 505px; width: 566px; height: 352px; }

  .card-bands { position: absolute; left: 0; top: 0; }

  /* Front: brand block */
  .brand-mark {
    position: absolute; left: 84px; top: 50px;
    width: 58px; height: 58px; background: var(--gold);
  }
  .brand-name {
    position: absolute; left: 160px; top: 52px;
    font-size: 40px; font-weight: 700; letter-spacing: 0.3px;
    text-transform: uppercase; line-height: 1;
  }
  .brand-tagline {
    position: absolute; left: 162px; top: 137px;
    font-size: 17.5px; font-weight: 600; color: var(--gold-deep);
    letter-spacing: 0.4px; text-transform: uppercase; line-height: 1;
  }

  /* Front: contact block */
  .person {
    position: absolute; right: 315px; top: 260px; text-align: right;
  }
  .person-name { font-size: 21px; font-weight: 700; line-height: 1.1; }
  .person-role { font-size: 16px; font-weight: 400; line-height: 1.25; }

  .contact-list {
    position: absolute; left: 293px; top: 249px; list-style: none;
    font-size: 16px; line-height: 21.5px;
  }
  .contact-list li { display: flex; align-items: center; }
  .contact-list svg { width: 12px; height: 12px; margin-right: 13px; flex: none; }

  .address {
    position: absolute; left: 103px; top: 327px;
    font-size: 16px; line-height: 1;
  }

  /* Back: appointment */
  .back-mark {
    position: absolute; left: 108px; top: 30px;
    width: 58px; height: 58px; background: var(--gold);
  }
  .appointment-title {
    position: absolute; left: 190px; top: 55px;
    font-size: 22px; font-weight: 600; color: var(--gold-text); line-height: 1;
  }
  .appointment-form {
    position: absolute; left: 80px; top: 118px; width: 404px;
    font-size: 14.5px; font-weight: 600;
  }
  .form-row { display: flex; align-items: baseline; height: 41px; }
  .form-label { white-space: nowrap; margin-right: 6px; }
  .form-line {
    flex: 1; height: 1px; border-bottom: 2px dotted var(--ink);
    transform: translateY(-3px);
  }
  .form-unit { margin: 0 4px; }
  .appointment-note {
    position: absolute; left: 0; right: 0; top: 297px;
    text-align: center; font-size: 17px; font-weight: 700; line-height: 1;
  }
</style>
</head>
<body>
<main class="canvas">

  <section class="card card-front" aria-label="Business card front">
    <svg class="card-bands" width="587" height="363" viewBox="0 0 587 363" aria-hidden="true">
      <defs>
        <linearGradient id="front-gold" x1="0" y1="0" x2="0" y2="1">
          <stop offset="0" stop-color="#c6a61f"/>
          <stop offset="0.5" stop-color="#f7ee2a"/>
          <stop offset="1" stop-color="#c9a91d"/>
        </linearGradient>
      </defs>
      <polygon points="0,198 402,198 380,224 0,224" fill="#111"/>
      <polygon points="414,190 587,190 587,363 0,363 0,228 384,228" fill="url(#front-gold)"/>
    </svg>

    <span class="brand-mark" aria-hidden="true"></span>
    <h1 class="brand-name">Harwell Dental Studio</h1>
    <p class="brand-tagline">Your smile is your gift to others</p>

    <div class="person">
      <p class="person-name">Marcus Ellery</p>
      <p class="person-role">Managing Director</p>
    </div>

    <ul class="contact-list">
      <li>
        <svg viewBox="0 0 12 12" aria-hidden="true"><path d="M2.4 0.6 4.3 2.5 3.2 4.1c.8 1.7 2 2.9 3.7 3.7l1.6-1.1 1.9 1.9-1.4 1.8C5 10.2 1.6 6.8 0.6 2.1Z" fill="#111"/></svg>
        044-987 654 321
      </li>
      <li>
        <svg viewBox="0 0 12 12" aria-hidden="true"><rect x="1" y="2.5" width="10" height="7" fill="#111"/><path d="M1 3 6 6.8 11 3" stroke="#f7ee2a" stroke-width="1" fill="none"/></svg>
        hello@harwelldental.com
      </li>
      <li>
        <svg viewBox="0 0 12 12" aria-hidden="true"><circle cx="6" cy="6" r="5" fill="none" stroke="#111" stroke-width="1.3"/><path d="M1 6h10M6 1c-2.4 3-2.4 7 0 10M6 1c2.4 3 2.4 7 0 10" stroke="#111" stroke-width="1" fill="none"/></svg>
        www.harwelldental.com
      </li>
    </ul>

    <p class="address">48 Linden Row, Brookfield Heights, 560214.</p>
  </section>

  <section class="card card-back" aria-label="Appointment card back">
    <svg class="card-bands" width="566" height="352" viewBox="0 0 566 352" aria-hidden="true">
      <defs>
        <linearGradient id="back-gold" x1="0" y1="0" x2="0" y2="1">
          <stop offset="0" stop-color="#c6a61f"/>
          <stop offset="0.5" stop-color="#f7ee2a"/>
          <stop offset="1" stop-color="#c9a91d"/>
        </linearGradient>
      </defs>
      <polygon points="0,238 386,238 364,263 0,263" fill="#111"/>
      <polygon points="398,230 566,230 566,352 0,352 0,267 368,267" fill="url(#back-gold)"/>
    </svg>

    <span class="back-mark" aria-hidden="true"></span>
    <h2 class="appointment-title">Your Next Appointment is</h2>

    <div class="appointment-form">
      <div class="form-row"><span class="form-label">Name :</span><span class="form-line"></span></div>
      <div class="form-row"><span class="form-label">Date :</span><span class="form-line"></span></div>
      <div class="form-row">
        <span class="form-label">Time :</span><span class="form-line"></span>
        <span class="form-unit">AM</span><span class="form-line"></span>
        <span class="form-unit">&nbsp;PM</span>
      </div>
    </div>

    <p class="appointment-note">If unable to keep appointment, kindly give 24hrs notice.</p>
  </section>

</main>
</body>
</html>
```